Letterhead for a German Distribution/Manufacturing Company

We need a professional Letterhead in a unique Design.
not to playful.
The Letterhead has to show show that we are a international company with headquater in Germany.
all details like adress, Vat Tax Number, Bank Accout, Eori, email, Company number has to be on the Letterhead.
for example use: VAT TAX DE5470318 Bank Account: Kestrel Bank IBAN DE412058731ß204683 Swift: MORV0417352 EORI 3150428697 Company Number: HRB 51806 Adress: VOLMINTA UG Ahornweg 7 Postal Code 06384 City Lindenfeld Country: Germany Email: info@volminta-example.com
the design can be colored but doesnt have to be
Industry/Entity Type
Manufacturing and international distribution
Requirements
Must have
- show that we are a international company with headquater in Germany. our company infos and logo

```html
<!DOCTYPE html>
<html lang="en">
<head>
<meta charset="utf-8">
<title>VOLMINTA Letterhead</title>
<link rel="stylesheet" href="https://fonts.googleapis.com/css2?family=Poppins:wght@400;500;600;700&display=swap">
<style>
:root{
  --ink:#111111;
  --band-dark:#111111;
  --band-grey:#b3b3b3;
  --rule:#a8a8a8;
  --paper:#ffffff;
  --backdrop:#dedede;
  --flag-black:#000000;
  --flag-red:#dd0000;
  --flag-gold:#ffce00;
  --sign-fill:#e9e9e9;
}
*{margin:0;padding:0;box-sizing:border-box}
html,body{width:672px;height:1200px;overflow:hidden;background:var(--backdrop)}
body{position:relative;font-family:'Poppins',sans-serif;color:var(--ink)}
.letterhead{
  position:absolute;left:16px;top:187px;width:940px;height:1215px;
  background:var(--paper);transform:scale(0.68);transform-origin:0 0;
  box-shadow:0 6px 18px rgba(0,0,0,.18);overflow:hidden;
}
.side-bands{position:absolute;left:0;top:0;width:60px;height:1215px}
.abs{position:absolute}
.brand{left:95px;top:98px;display:flex;align-issues:center;align-items:center;gap:14px}
.brand-dot{width:44px;height:44px;border-radius:50%;background:var(--ink)}
.brand-name{font-size:46px;font-weight:400;letter-spacing:.5px;line-height:1}
.hq{left:570px;top:106px;font-size:14.5px;font-weight:600;line-height:1.25}
.hq-row{display:flex;align-items:flex-start;gap:9px;margin:8px 0 0 28px}
.flag{width:32px;height:32px;display:flex;flex-direction:column;margin-top:2px}
.flag span{flex:1}
.flag .b{background:var(--flag-black)}.flag .r{background:var(--flag-red)}.flag .g{background:var(--flag-gold)}
.sender{left:94px;top:242px}
.sender-name{font-size:20px;font-weight:700;line-height:1.2}
.sender-role{font-size:15px;font-weight:500;line-height:1.2;margin-bottom:14px}
.contact{display:grid;grid-template-columns:26px auto;font-size:13.5px;line-height:17px;row-gap:7px}
.contact dt{font-weight:700}
.date{left:578px;top:368px;font-size:13.5px;font-weight:600}
.body-text{left:97px;top:434px;width:756px;font-size:14.5px;line-height:16.6px}
.body-text p{margin-bottom:31px}
.signature{left:92px;top:778px;width:130px;height:48px;background:var(--sign-fill);border-radius:4px}
.footer-rule{left:92px;top:1024px;width:751px;height:2px;background:var(--rule)}
.footer-col{top:1046px;font-size:12.5px;line-height:16px}
.footer-col.left{left:178px}
.footer-col.right{left:447px}
.f-row{display:flex;gap:5px;margin-bottom:5px}
.f-row b{font-weight:700;white-space:nowrap}
.f-row.indent{padding-left:21px}
.addr-lines{max-width:130px}
.ico{width:15px;height:15px;flex:none;margin-top:1px}
</style>
</head>
<body>
<div class="letterhead">
  <svg class="side-bands" viewBox="0 0 60 1215" aria-hidden="true">
    <rect x="0" y="0" width="31" height="1215" fill="var(--band-dark)"/>
    <rect x="31" y="0" width="28" height="1215" fill="var(--band-grey)"/>
    <polygon points="31,782 59,758 59,766 31,790" fill="var(--paper)"/>
    <polygon points="31,934 59,910 59,918 31,942" fill="var(--paper)"/>
  </svg>

  <div class="abs brand">
    <div class="brand-dot"></div>
    <div class="brand-name">VOLMINTA</div>
  </div>

  <div class="abs hq">
    INTERNATIONAL COMPANY
    <div class="hq-row">
      <div class="flag"><span class="b"></span><span class="r"></span><span class="g"></span></div>
      <div>HEADQUARTER IN<br>GERMANY</div>
    </div>
  </div>

  <div class="abs sender">
    <div class="sender-name">LENA HARTMANN</div>
    <div class="sender-role">chief director</div>
    <dl class="contact">
      <dt>A:</dt><dd>Unit 14, Harrow Court 58 Mill Lane,<br>London, Greater London N4 2QT, GB</dd>
      <dt>W:</dt><dd>www.volminta-example.com</dd>
      <dt>P:</dt><dd>415286093</dd>
    </dl>
  </div>

  <div class="abs date">DATE: 03.04.2023</div>

  <div class="abs body-text">
    <p>Lorem Ipsum is simply dummy text of the printing and typesetting industry. Lorem Ipsum has been the industry's standard dummy text ever since the 1500s, when an unknown printer took a galley of type and scrambled it to make a type specimen book. It has survived not only five centuries, but also the leap into electronic typesetting, remaining essentially unchanged.</p>
    <p>It is a long established fact that a reader will be distracted by the readable content of a page when looking at its layout. The point of using Lorem Ipsum is that it has a more-or-less normal distribution of letters, as opposed to using 'Content here, content here', making it look like readable English. Many desktop publishing packages and web page editors now use Lorem Ipsum as their default model text, and a search for 'lorem ipsum' will uncover many web sites still in their infancy. Various versions have evolved over the years, sometimes by accident, sometimes on purpose (injected humour and the like).</p>
    <p>There are many variations of passages of Lorem Ipsum available, but the majority have suffered alteration in some form, by injected humour, or randomised words which don't look even slightly believable. If you are going to use a passage of Lorem Ipsum, you need to be sure there isn't anything embarrassing hidden in the middle of text.</p>
  </div>

  <div class="abs signature" role="img" aria-label="Handwritten signature of the sender"></div>

  <div class="abs footer-rule"></div>

  <div class="abs footer-col left">
    <div class="f-row">
      <svg class="ico" viewBox="0 0 16 16"><rect x="2" y="2" width="12" height="12" fill="none" stroke="currentColor" stroke-width="2"/><path d="M5 11h6M8 5v6" stroke="currentColor" stroke-width="1.6"/></svg>
      <span><b>COMPANY NUMBER:</b> HRB 51806</span>
    </div>
    <div class="f-row">
      <svg class="ico" viewBox="0 0 16 16"><path d="M8 1a5 5 0 0 0-5 5c0 4 5 9 5 9s5-5 5-9a5 5 0 0 0-5-5z" fill="none" stroke="currentColor" stroke-width="1.8"/><circle cx="8" cy="6" r="1.8" fill="currentColor"/></svg>
      <span><b>ADDRESS:</b></span>
      <span class="addr-lines">VOLMINTA UG Ahornweg 7<br>Postal Code 06384<br>City Lindenfeld</span>
    </div>
    <div class="f-row">
      <svg class="ico" viewBox="0 0 16 16"><path d="M3 1v14" stroke="currentColor" stroke-width="1.8"/><path d="M3 2h10l-2.5 3.5L13 9H3z" fill="currentColor"/></svg>
      <span><b>COUNTRY:</b> Germany</span>
    </div>
  </div>

  <div class="abs footer-col right">
    <div class="f-row">
      <svg class="ico" viewBox="0 0 16 16"><rect x="3" y="1" width="10" height="14" fill="none" stroke="currentColor" stroke-width="1.8"/><path d="M5 5h6M5 8h6M5 11h4" stroke="currentColor" stroke-width="1.3"/></svg>
      <span><b>VAT TAX :</b> DE5470318</span>
    </div>
    <div class="f-row">
      <svg class="ico" viewBox="0 0 16 16"><circle cx="8" cy="8" r="6.5" fill="none" stroke="currentColor" stroke-width="1.8"/><circle cx="8" cy="6.5" r="2" fill="currentColor"/><path d="M4.5 12.5a4 4 0 0 1 7 0" fill="currentColor"/></svg>
      <span><b>BANK ACCOUNT:</b>&nbsp; Kestrel Bank IBAN DE412058731ß204683</span>
    </div>
    <div class="f-row indent"><span><b>SWIFT:</b> MORV0417352</span></div>
    <div class="f-row indent"><span><b>EORI:</b> 3150428697</span></div>
    <div class="f-row">
      <svg class="ico" viewBox="0 0 16 16"><rect x="1" y="3" width="14" height="10" fill="currentColor"/><path d="M1 3l7 6 7-6" fill="none" stroke="#fff" stroke-width="1.3"/></svg>
      <span><b>EMAIL:</b> info@volminta-example.com</span>
    </div>
  </div>
</div>
</body>
</html>
```